TA BRAMLEY BUSINESS CARD DESIGN PROJECT

We need to utilize our logo that was expertly created on PixelHarbor and now need to match this with a business card design.

```html
<!DOCTYPE html>
<html lang="en">
<head>
<meta charset="utf-8">
<title>TA BRAMLEY Business Card</title>
<link href="https://fonts.googleapis.com/css2?family=Montserrat:wght@400;500;700;800&display=swap" rel="stylesheet">
<style>
  :root {
    --brand-blue: #0f57ab;
    --ink: #2b2b2b;
    --card: #ffffff;
    --backdrop: #d9d9d9;
  }
  * { box-sizing: border-box; margin: 0; padding: 0; }
  html, body { width: 1200px; height: 800px; overflow: hidden; }
  body {
    background: var(--backdrop);
    font-family: "Montserrat", sans-serif;
    position: relative;
  }
  .card {
    position: absolute;
    background: var(--card);
    border-radius: 26px;
    border-bottom: 4px solid var(--brand-blue);
    box-shadow: 0 10px 24px rgba(0,0,0,0.18);
  }
  /* Front: portrait */
  .card-front {
    left: 110px; top: 110px;
    width: 340px; height: 580px;
    padding: 56px 30px 30px;
  }
  .brand-lockup {
    display: flex; align-items: center; justify-content: center; gap: 12px;
  }
  .brand-dot {
    width: 22px; height: 22px; border-radius: 50%;
    background: var(--brand-blue);
  }
  .brand-name {
    font-weight: 800; color: var(--brand-blue);
    letter-spacing: 0.12em; font-size: 30px;
  }
  .person { text-align: center; margin-top: 40px; }
  .person-name {
    font-weight: 800; color: var(--brand-blue); font-size: 22px;
  }
  .person-role {
    color: var(--ink); font-size: 15px; margin-top: 4px;
  }
  .dot-row { display: block; margin: 0 auto; }
  .contact-rule { margin-top: 56px; }
  .contact-lines {
    text-align: center; color: var(--ink);
    font-size: 15px; line-height: 1.55; margin: 10px 0 16px;
  }
  .address-lines {
    text-align: center; color: var(--ink);
    font-size: 15px; line-height: 1.55; margin-top: 10px;
  }
  /* Back: landscape */
  .card-back {
    left: 540px; top: 240px;
    width: 580px; height: 350px;
    display: flex; align-items: center; justify-content: center;
  }
  .card-back .brand-dot { width: 44px; height: 44px; }
  .card-back .brand-name { font-size: 62px; letter-spacing: 0.1em; }
  .card-back .brand-lockup { gap: 22px; }
</style>
</head>
<body>

<section class="card card-front">
  <div class="brand-lockup">
    <span class="brand-dot"></span>
    <span class="brand-name">TA BRAMLEY</span>
  </div>

  <div class="person">
    <p class="person-name">MARCUS HALE</p>
    <p class="person-role">Managing Director</p>
  </div>

  <svg class="dot-row contact-rule" width="280" height="34" viewBox="0 0 280 34" aria-hidden="true">
    <g fill="var(--brand-blue)">
      <circle cx="6" cy="17" r="3"/><circle cx="18" cy="17" r="4"/><circle cx="32" cy="17" r="5"/>
      <circle cx="48" cy="17" r="6"/><circle cx="66" cy="17" r="7"/><circle cx="86" cy="17" r="8"/>
      <circle cx="112" cy="17" r="15"/><circle cx="146" cy="17" r="15"/><circle cx="180" cy="17" r="15"/>
      <circle cx="206" cy="17" r="8"/><circle cx="226" cy="17" r="7"/><circle cx="244" cy="17" r="6"/>
      <circle cx="259" cy="17" r="5"/><circle cx="271" cy="17" r="4"/>
    </g>
    <!-- phone -->
    <path d="M106 10 q-2 0 -2 3 q1 8 10 11 q3 0 3 -2 l-3 -3 l-2 1 q-3 -2 -4 -5 l1 -2 z" fill="#fff"/>
    <!-- mail -->
    <rect x="138" y="11" width="16" height="12" rx="1.5" fill="#fff"/>
    <path d="M138 12 l8 6 l8 -6" fill="none" stroke="var(--brand-blue)" stroke-width="1.5"/>
    <!-- globe -->
    <circle cx="180" cy="17" r="8" fill="none" stroke="#fff" stroke-width="1.6"/>
    <ellipse cx="180" cy="17" rx="3.5" ry="8" fill="none" stroke="#fff" stroke-width="1.3"/>
    <line x1="172" y1="17" x2="188" y2="17" stroke="#fff" stroke-width="1.3"/>
  </svg>

  <div class="contact-lines">
    <p>123 456 789</p>
    <p>info@yourgmail.com</p>
    <p>www.yourwebsite.com</p>
  </div>

  <svg class="dot-row" width="280" height="34" viewBox="0 0 280 34" aria-hidden="true">
    <g fill="var(--brand-blue)">
      <circle cx="6" cy="17" r="3"/><circle cx="18" cy="17" r="4"/><circle cx="32" cy="17" r="5"/>
      <circle cx="48" cy="17" r="6"/><circle cx="66" cy="17" r="7"/><circle cx="88" cy="17" r="9"/>
      <circle cx="140" cy="17" r="15"/>
      <circle cx="192" cy="17" r="9"/><circle cx="214" cy="17" r="7"/><circle cx="232" cy="17" r="6"/>
      <circle cx="248" cy="17" r="5"/><circle cx="262" cy="17" r="4"/><circle cx="274" cy="17" r="3"/>
    </g>
    <!-- pin -->
    <path d="M140 27 q-7 -8 -7 -12 a7 7 0 0 1 14 0 q0 4 -7 12 z" fill="#fff"/>
    <circle cx="140" cy="15" r="2.6" fill="var(--brand-blue)"/>
  </svg>

  <div class="address-lines">
    <p>Your address, City</p>
    <p>State, Zip 1234</p>
  </div>
</section>

<section class="card card-back">
  <div class="brand-lockup">
    <span class="brand-dot"></span>
    <span class="brand-name">TA BRAMLEY</span>
  </div>
</section>

</body>
</html>
```